Want to fly? Flight school needs a roll up

Hello designers

We are a small aviation club with around 100 members. We love flying and therefore offer free flight lessons for young people at our glider flight school.
The young people only have to pay a flat rate of €300 for the aircraft until their first solo flight.
To advertise the flight school we now need a roll up banner measuring 85cm x 200cm. You can find the data sheet for the banner in the appendix.
Content of the roll up banner:
Advertising for our flight school so that we can attract new members
The banner should be designed in our club colors blue/white
The banner is aimed at all people who want to get a glider license
A great offer for young people up to the age of 25 should be placed on the banner with a reference to the text “Offer only applies to people up to the age of 25. Included in the flat rate of €300 is training on the glider up to the first "solo flight"
The banner is intended to advertise training with a glider. Therefore the wish would be for a glider to be depicted

Here is a link to our current homepage

https://www.lgk-tarnholm.de/

https://www.vidoplex.example/watch?v=Qk7pL2xNz9c

Target Market(s)

Young people from 14 years to 30 years

Colors
0054AA
0677BA
7BADD7
CADEEF
E8F1F8

Requirements
Nice to have
• Glider / club logo
Should not have
• Too much text

```html
<!DOCTYPE html>
<html lang="en">
<head>
<meta charset="utf-8">
<title>Glider Flight School Roll-Up</title>
<link rel="stylesheet" href="https://fonts.googleapis.com/css2?family=Oswald:wght@500;600&family=Montserrat:wght@800&display=swap">
<style>
  :root {
    --club-blue: #1111a8;
    --club-blue-dark: #0a0c86;
    --club-blue-light: #3b4fd0;
    --navy: #0d0f3a;
    --white: #ffffff;
    --ink: #0a0a12;
  }
  * { margin: 0; padding: 0; box-sizing: border-box; }
  html, body { width: 1200px; height: 4000px; overflow: hidden; background: var(--white); }
  .banner { position: relative; width: 1200px; height: 4000px; overflow: hidden; background: var(--club-blue); }

  .photo { position: absolute; }
  .photo-sky { left: 0; top: 0; width: 1200px; height: 760px;
    background: linear-gradient(160deg, #5a6cc8 0%, #8fa3de 40%, #c9d4f0 65%, #7f93d8 100%);
    clip-path: polygon(1090px 0, 1200px 0, 1200px 700px, 424px 715px); }
  .photo-field { left: 0; top: 2300px; width: 1200px; height: 1420px;
    background: linear-gradient(180deg, #8ea6dc 0%, #c6d3ea 20%, #8da07a 42%, #5b6e45 56%, #a83a52 72%, #3a3f6a 100%);
    clip-path: polygon(0 40px, 1200px 140px, 1200px 100%, 0 100%); }

  .shapes { position: absolute; left: 0; top: 0; width: 1200px; height: 4000px; }

  .club-mark { position: absolute; left: 92px; top: 142px; width: 412px; height: 412px; border-radius: 50%;
    background: var(--white); display: flex; align-items: center; justify-content: center; text-align: center;
    font-family: "Oswald", sans-serif; font-weight: 600; font-size: 60px; line-height: 1.05;
    color: var(--club-blue); text-transform: uppercase; }

  .photo-round { border-radius: 50%; border: 10px solid var(--white); }
  .photo-cockpit { left: 640px; top: 824px; width: 640px; height: 640px;
    background: radial-gradient(circle at 40% 40%, #e9edf5 0%, #a8b3c8 45%, #4a5570 100%); }
  .photo-canopy { left: 710px; top: 1790px; width: 600px; height: 600px;
    background: radial-gradient(circle at 55% 55%, #f1f3f6 0%, #b6bfb0 45%, #56704a 100%); }

  .line { position: absolute; white-space: nowrap; text-transform: uppercase; line-height: 1; }
  .headline .line { left: 115px; color: var(--white); font-family: "Oswald", sans-serif; font-weight: 500; }
  .headline .lead { top: 812px; font-size: 104px; }
  .headline .price { top: 970px; font-size: 218px; font-weight: 600; }
  .headline .goal-1 { top: 1345px; font-size: 118px; }
  .headline .goal-2 { top: 1540px; font-size: 118px; }

  .age-note .line { left: 140px; color: var(--white); font-family: "Montserrat", sans-serif; font-weight: 800; font-size: 78px; }
  .age-note .l1 { top: 1815px; }
  .age-note .l2 { top: 1945px; }
  .age-ribbon { left: 206px; top: 2150px; color: var(--club-blue-dark);
    font-family: "Montserrat", sans-serif; font-weight: 800; font-size: 90px; }

  .training .line { left: 149px; color: var(--ink); font-family: "Oswald", sans-serif; font-weight: 600; font-size: 140px; }
  .training .t1 { top: 2680px; }
  .training .t2 { top: 2893px; }

  .footer { position: absolute; left: 0; top: 3673px; width: 1200px; height: 327px;
    background: linear-gradient(180deg, rgba(13,15,58,0.5) 0%, var(--navy) 30%);
    display: flex; align-items: center; justify-content: center; padding-top: 20px; }
  .web { color: var(--white); font-family: "Oswald", sans-serif; font-weight: 600; font-size: 116px; white-space: nowrap; }
</style>
</head>
<body>
<main class="banner">
  <div class="photo photo-sky" role="img" aria-label="White glider flying against a blue cloudy sky"></div>

  <svg class="shapes" viewBox="0 0 1200 4000" aria-hidden="true">
    <polygon points="0,0 300,0 0,170" fill="var(--club-blue-dark)" opacity="0.8"/>
    <polygon points="424,715 1090,0 1130,0 470,740" fill="var(--club-blue-light)" opacity="0.7"/>
    <polygon points="0,2250 1200,2360 1200,2440 0,2340" fill="var(--club-blue-light)" opacity="0.7"/>
    <polygon points="127,2106 1150,2106 1150,2291 206,2291" fill="var(--white)"/>
  </svg>

  <div class="photo photo-field" role="img" aria-label="Glider on tow above a green airfield with a red and white tow plane in the foreground"></div>

  <div class="club-mark">Luftsport-<br>gruppe<br>Tarnholm</div>

  <div class="photo photo-round photo-cockpit" role="img" aria-label="Instructor and student seated in a glider cockpit"></div>
  <div class="photo photo-round photo-canopy" role="img" aria-label="Pilot in an open glider canopy on the airfield"></div>

  <h1 class="headline">
    <span class="line lead">Offer only</span>
    <span class="line price">300€</span>
    <span class="line goal-1">Till first</span>
    <span class="line goal-2">Solo flight</span>
  </h1>

  <p class="age-note">
    <span class="line l1">Offer only</span>
    <span class="line l2">Applies for</span>
  </p>
  <p class="line age-ribbon">Age of 25</p>

  <h2 class="training">
    <span class="line t1">Is training</span>
    <span class="line t2">On the glider</span>
  </h2>

  <footer class="footer"><span class="web">www.lgk-tarnholm.de</span></footer>
</main>
</body>
</html>
```